Business Card Design

I need a business card design for my new business based on Long Island, NY also serving NYC called Pawhaven Retreat. I have built a website with cardmint that can be looked at as a basis for the card. It is pawhavenretreat.com.

I board Labrador Retrievers in my home. Specialize in one breed. Cage free environment. Dogs have full run of home and fenced in property. Pawhaven Retreat is a one-of-a-kind, high-quality dog-boarding provider serving specifically Labrador Retrievers. By working with a dog I am comfortable with, I am able to offer the best care for all pets that come through my door. I work with Lab owners in the Long Island/NYC area to provide an
in-home safe, reliable and fun environment for daycare and overnight stays.

I provide a unique boarding experience for Labrador Retrievers on Long Island. Your Lab should be well mannered, housebroken and good with other dogs. Provided your pet is well mannered and house trained, my boarding services allow dogs to experience a cage-free stay while having free roam of my home and property. This allows owners a unique alternative to a kennel, giving pets the chance to experience a home away from home rather than chain linked fences and cold concrete floors.
As a guest at Pawhaven Retreat, your dog will get:

4-star kibble
Access to my in-ground pool
All-natural snack selection
Companionship of other retrievers including my two
Full run of entire home and fenced-in backyard
Photos AND videos posted to Snapgram so you can see your dog having fun while away
Toys, bones and affection

I think it is important to have a pic of the 3 colored labs below. Also the picture of my own personal labs ..the white one with the black puppy. Maybe some paw prints. If using any imagery that MUST look EXACTLY like labrador retriever no generic dogs. Thank you
Updates

The Back of the Card should have the following: The background should be one of the pictures I sent (white dog in pool or another pic I included) At Pawhaven Retreat your Lab gets: Cage Free Environment Full run of my home and fenced in yard In-ground pool Toys and affection Companionship of other Labrador Retrievers Photos and Videos posted Snapgram of your loved one FRONT OF THE CARD: should include picture of the 3 labs (yellow white brown) OR picture of white dog in pool. Pawhaven Retreat should be in larger font than the rest. the following can be in any order. Tom Pelley Commack, NY in Central Long Island pawhavenretreat.com 631-555-0192

Industry/Entity Type

Environment

Contact Information for Business Card

Pawhaven Retreat
Commack, NY
Tom Pelley
hello@pawhavenretreat.com
631-555-0192

```html
<!DOCTYPE html>
<html lang="en">
<head>
<meta charset="utf-8">
<title>Pawhaven Retreat – Business Card</title>
<link href="https://fonts.googleapis.com/css2?family=Roboto:wght@300;400&display=swap" rel="stylesheet">
<style>
  :root {
    --page-bg: #e9e6e1;
    --card-white: #ffffff;
    --card-grey: #e4e4e4;
    --fade-light: #f1f1f0;
    --fade-mid: #d9d9d7;
    --photo-green: #7f8f5a;
    --photo-dark: #2e2622;
    --photo-cream: #e8dcc0;
    --arc-brown: #8a6c5c;
    --ink: #1e1e1e;
    --ink-soft: #3a3a3a;
  }
  * { box-sizing: border-box; margin: 0; padding: 0; }
  html, body { width: 1200px; height: 858px; overflow: hidden; }
  body {
    background: var(--page-bg);
    font-family: "Roboto", Arial, sans-serif;
    color: var(--ink);
    position: relative;
  }
  .card {
    position: absolute;
    top: 279px;
    width: 525px;
    height: 300px;
    overflow: hidden;
    box-shadow: 0 6px 18px rgba(0,0,0,.18);
  }
  /* FRONT */
  .card-front { left: 45px; background: var(--card-white); }
  .front-fade {
    position: absolute; inset: 0;
    background: linear-gradient(135deg, var(--fade-light) 0%, var(--fade-mid) 55%, var(--fade-light) 100%);
  }
  .front-art { position: absolute; inset: 0; }
  .front-details {
    position: absolute;
    right: 26px; top: 26px;
    text-align: right;
    font-weight: 300;
  }
  .owner { font-size: 19px; letter-spacing: .3px; margin-bottom: 16px; }
  .contact-line {
    font-size: 13px;
    display: flex; align-items: center; justify-content: flex-end; gap: 8px;
    margin-bottom: 6px;
  }
  .contact-line svg { width: 12px; height: 12px; fill: var(--ink); }
  .business-name {
    position: absolute;
    right: 22px; bottom: 22px;
    font-size: 24px; font-weight: 300;
    letter-spacing: .2px;
    white-space: nowrap;
  }
  /* BACK */
  .card-back {
    left: 630px;
    background: linear-gradient(180deg, var(--card-white) 0%, var(--card-grey) 100%);
    border-bottom: 5px solid var(--photo-dark);
    padding: 24px 26px;
  }
  .back-heading {
    display: flex; align-items: center; gap: 10px;
    font-size: 17px; font-weight: 300;
    margin-bottom: 18px;
  }
  .brand-dot {
    width: 28px; height: 28px; border-radius: 50%;
    background: var(--ink); flex: none;
  }
  .perks { list-style: none; }
  .perks li {
    display: flex; align-items: flex-start; gap: 9px;
    font-size: 13px; font-weight: 300; line-height: 1.25;
    color: var(--ink-soft);
    margin-bottom: 3px;
  }
  .perks li::before {
    content: "";
    width: 9px; height: 9px; border-radius: 50%;
    background: var(--ink); flex: none; margin-top: 3px;
  }
</style>
</head>
<body>

<section class="card card-front">
  <div class="front-fade" role="img" aria-label="Faded photo of a white Labrador Retriever with a black Labrador puppy"></div>
  <svg class="front-art" viewBox="0 0 525 300" preserveAspectRatio="none">
    <defs>
      <linearGradient id="labs" x1="0" y1="0" x2="1" y2="1">
        <stop offset="0" stop-color="var(--photo-dark)"/>
        <stop offset=".45" stop-color="var(--photo-cream)"/>
        <stop offset=".75" stop-color="var(--photo-dark)"/>
        <stop offset="1" stop-color="var(--photo-green)"/>
      </linearGradient>
    </defs>
    <path role="img" aria-label="Photo of three Labrador Retrievers: black, yellow and chocolate, sitting on grass"
          d="M0 0 H150 Q250 150 150 300 H0 Z" fill="url(#labs)"/>
    <path d="M150 0 Q250 150 150 300" fill="none" stroke="var(--arc-brown)" stroke-width="5"/>
  </svg>

  <div class="front-details">
    <p class="owner">NY Tom Pelley</p>
    <p class="contact-line">631-555-0192
      <svg viewBox="0 0 24 24"><path d="M6.6 10.8a15.1 15.1 0 0 0 6.6 6.6l2.2-2.2c.3-.3.7-.4 1-.2 1.1.4 2.3.6 3.6.6.6 0 1 .4 1 1V20c0 .6-.4 1-1 1A17 17 0 0 1 3 4c0-.6.4-1 1-1h3.5c.6 0 1 .4 1 1 0 1.3.2 2.5.6 3.6.1.3 0 .7-.2 1z"/></svg>
    </p>
    <p class="contact-line">hello@pawhavenretreat.com
      <svg viewBox="0 0 24 24"><path d="M2 5h20v14H2z M4 7v.5l8 5 8-5V7z" fill-rule="evenodd"/></svg>
    </p>
  </div>
  <h1 class="business-name">Pawhaven Retreat Commack</h1>
</section>

<section class="card card-back">
  <h2 class="back-heading"><span class="brand-dot"></span>As a guest at Pawhaven Retreat, your dog will get</h2>
  <ul class="perks">
    <li>4-star kibble</li>
    <li>Access to my in-ground pool</li>
    <li>All-natural snack selection</li>
    <li>Companionship of other retrievers including my two</li>
    <li>Full run of entire home and fenced-in backyard</li>
    <li>Photos AND videos posted to Snapgram so you can see your dog having fun while away</li>
    <li>Toys, bones and affection</li>
  </ul>
</section>

</body>
</html>
```